Dwelvano - "Where Pest Control is Free for Life..." Please see pitch deck...

Project goal, that this is a reusable template, not a one-off card
Brand and design direction, follow the logo, use the brand palette (with a color swatch table), typography and layout guidance
The John Doe placeholder content as a clean field-by-field table (name, title, company, address, office, cell, fax, email, dwelvano.com)
Print specs, 3.5 × 2 in trim, 0.125 in bleed, 300 DPI, CMYK, crop marks
Deliverables, layered editable PSD (your primary ask) plus vector .AI/.EPS and a press-ready PDF/X-1a, with fonts packaged
What you'll provide (logo, colors, fonts)
Process and sign-off, concept first, then full file package on approval.
Populate every field with this John Doe placeholder data so we can see the layout fully built out. We will replace it per person.
Name John Doe
Title Title / Position
Company Dwelvano
Address 48 Harbor Lane, Suite 210, Pensacola, FL 32502
Office (850) 555-0142
Cell (850) 555-0178
Fax (850) 555-0186
Email johndoe@dwelvano.com
Website dwelvano.com

We need the working, editable source files so we can update them ourselves, plus a ready-to-print export:
1. Photoshop (.PSD) — fully layered and editable, with each contact field on its own labeled text layer. This is the primary requested format.
2. Vector source — the press-standard editable format, Adobe Illustrator (.AI) and/or .EPS, since vector is preferred for crisp text and logos at print.
3. Print-ready PDF — press-quality (PDF/X-1a), CMYK, with bleed and crop marks, both sides.
4. Packaged fonts and links — include or list all fonts used, and package any linked assets so the files open correctly on our end.

Why both PSD and vector
The PSD covers our request directly and is easy for us to edit. Vector (.AI/.EPS) is what most commercial printers actually prefer for type and logos because it stays razor-sharp at any size. Providing both keeps us flexible no matter which printer we use. Have fun and keep it modern and cool the designer of the logo did a great job, see what you can do.

```html
<!DOCTYPE html>
<html lang="en">
<head>
<meta charset="utf-8">
<title>Dwelvano Business Card</title>
<link rel="stylesheet" href="https://fonts.googleapis.com/css2?family=Montserrat:wght@400;500;800&display=swap">
<style>
  :root {
    --canvas: #3a3a3c;
    --card-navy: #0b1226;
    --brand-teal: #15b4c8;
    --ink-white: #ffffff;
    --ink-soft: #e8edf3;
  }
  * { box-sizing: border-box; margin: 0; padding: 0; }
  html, body {
    width: 1200px; height: 875px; overflow: hidden;
    background: var(--canvas);
    font-family: "Montserrat", sans-serif;
  }
  .stage { position: relative; width: 1200px; height: 875px; }
  .card {
    position: absolute;
    width: 640px; height: 366px;
    background: var(--card-navy);
    border-radius: 22px;
    box-shadow: 0 18px 40px rgba(0,0,0,.45);
  }
  .card--front { left: 60px; top: 70px; display: flex; align-items: center; justify-content: center; }
  .card--back { left: 500px; top: 440px; }

  .wordmark { display: flex; align-items: center; gap: 14px; color: var(--ink-white); font-weight: 800; letter-spacing: -1px; white-space: nowrap; }
  .wordmark__square { background: var(--brand-teal); border-radius: 6px; flex: none; }
  .card--front .wordmark { font-size: 92px; }
  .card--front .wordmark__square { width: 58px; height: 58px; }

  .card--back .wordmark { position: absolute; left: 48px; top: 150px; font-size: 50px; gap: 10px; }
  .card--back .wordmark__square { width: 32px; height: 32px; border-radius: 4px; }

  .divider { position: absolute; left: 362px; top: 52px; width: 1.5px; height: 262px; background: var(--brand-teal); }

  .contact { position: absolute; left: 386px; top: 58px; color: var(--ink-soft); white-space: nowrap; }
  .contact__name { font-weight: 800; font-size: 29px; color: var(--brand-teal); letter-spacing: .5px; line-height: 1.05; }
  .contact__company { font-weight: 500; font-size: 17px; margin-top: 4px; }
  .contact__address { font-size: 14.5px; line-height: 1.4; margin-top: 16px; }
  .contact__list { list-style: none; margin-top: 14px; font-size: 14.5px; }
  .contact__item { display: flex; align-items: center; gap: 9px; line-height: 1.55; }
  .contact__icon { width: 13px; height: 13px; fill: var(--brand-teal); flex: none; }
</style>
</head>
<body>
<main class="stage">
  <section class="card card--front" aria-label="Card front">
    <div class="wordmark"><span class="wordmark__square"></span>Dwelvano</div>
  </section>

  <section class="card card--back" aria-label="Card back">
    <div class="wordmark"><span class="wordmark__square"></span>Dwelvano</div>
    <div class="divider"></div>
    <div class="contact">
      <p class="contact__name">JOHN DOE</p>
      <p class="contact__company">Company Dwelvano</p>
      <p class="contact__address">48 Harbor Lane, Suite 210,<br>Pensacola, FL 32502</p>
      <ul class="contact__list">
        <li class="contact__item">
          <svg class="contact__icon" viewBox="0 0 24 24"><path d="M6.6 10.8a15.1 15.1 0 0 0 6.6 6.6l2.2-2.2a1 1 0 0 1 1-.25 11.4 11.4 0 0 0 3.6.57 1 1 0 0 1 1 1V20a1 1 0 0 1-1 1A17 17 0 0 1 3 4a1 1 0 0 1 1-1h3.5a1 1 0 0 1 1 1c0 1.25.2 2.45.57 3.57a1 1 0 0 1-.25 1z"/></svg>
          (850) 555-0142
        </li>
        <li class="contact__item">
          <svg class="contact__icon" viewBox="0 0 24 24"><path d="M7 1h10a2 2 0 0 1 2 2v18a2 2 0 0 1-2 2H7a2 2 0 0 1-2-2V3a2 2 0 0 1 2-2zm0 3v14h10V4zm5 15.5a1.2 1.2 0 1 0 0 2.4 1.2 1.2 0 0 0 0-2.4z"/></svg>
          (850) 555-0178
        </li>
        <li class="contact__item">
          <svg class="contact__icon" viewBox="0 0 24 24"><path d="M6 2h12v5H6zM4 8h16a2 2 0 0 1 2 2v7h-4v5H6v-5H2v-7a2 2 0 0 1 2-2zm4 8v4h8v-4z"/></svg>
          (850) 555-0186
        </li>
        <li class="contact__item">
          <svg class="contact__icon" viewBox="0 0 24 24"><path d="M2 5h20v14H2zm2 2v.4l8 5.2 8-5.2V7zm0 2.8V17h16V9.8l-8 5.2z"/></svg>
          johndoe@dwelvano.com
        </li>
        <li class="contact__item">
          <svg class="contact__icon" viewBox="0 0 24 24"><path d="M12 2a10 10 0 1 0 0 20 10 10 0 0 0 0-20zm6.9 6h-3a15 15 0 0 0-1.3-3.9A8 8 0 0 1 18.9 8zM12 4c.9 1.2 1.6 2.6 2 4h-4c.4-1.4 1.1-2.8 2-4zM4.3 14a8 8 0 0 1 0-4h3.4a16 16 0 0 0 0 4zm.8 2h3a15 15 0 0 0 1.3 3.9A8 8 0 0 1 5.1 16zm3-8h-3a8 8 0 0 1 4.3-3.9A15 15 0 0 0 8.1 8zM12 20c-.9-1.2-1.6-2.6-2-4h4c-.4 1.4-1.1 2.8-2 4zm2.3-6H9.7a14 14 0 0 1 0-4h4.6a14 14 0 0 1 0 4zm.3 5.9a15 15 0 0 0 1.3-3.9h3a8 8 0 0 1-4.3 3.9zm1.7-5.9a16 16 0 0 0 0-4h3.4a8 8 0 0 1 0 4z"/></svg>
          dwelvano.com
        </li>
      </ul>
    </div>
  </section>
</main>
</body>
</html>
```